Create a memorable Web Design for real estate branding

we are a Minnepolis brokerage and boutique housing specialist with over 27 years of experience in the Global furnished housing industry, servicing the Greater Los Angeles area. Specializing in “warm environments” we offer a customized approach to satisfying our guests and client’s needs by offering a wide array of options in highly desirable areas. Additionally, Lantern Dwelling Partners offers assistance and expertise to home buyers, sellers and investors.

Industry/Entity Type

Real Estate

Number of Pages Required

1 page

Font styles to use
Serif
Sans Serif
Decorative

```html
<!DOCTYPE html>
<html lang="en">
<head>
<meta charset="utf-8">
<title>Lantern Dwelling Partners — Real Estate</title>
<link rel="stylesheet" href="https://fonts.googleapis.com/css2?family=Open+Sans:wght@400;600;700&family=Montserrat:wght@400;500;700&display=swap">
<style>
:root{
  --teal:#17a88c;
  --green:#8cc63f;
  --ink:#333333;
  --muted:#555555;
  --dark:#151515;
  --footer:#222222;
  --footer-base:#181818;
  --soft:#f4f4f4;
  --line:#dcdcdc;
  --price:#e0312b;
}
*{box-sizing:border-box;margin:0;padding:0}
html,body{width:1200px;height:2341px;overflow:hidden}
body{position:relative;font-family:"Open Sans",Arial,sans-serif;color:var(--ink);background:#fff}
.abs{position:absolute}

.topbar{left:0;top:0;width:1200px;height:47px;background:var(--teal);color:#fff;font-size:13px;font-weight:600}
.topbar .welcome{left:100px;top:15px}
.topbar .phone{left:796px;top:15px;display:flex;gap:10px;align-items:center}
.topbar .sep{left:908px;top:0;width:1px;height:47px;background:rgba(255,255,255,.35)}
.topbar .mail{left:930px;top:15px;display:flex;gap:12px;align-items:center}

.header{left:0;top:47px;width:1200px;height:97px;background:#fff}
.brand{display:flex;align-items:center;gap:12px}
.brand .mark{width:26px;height:26px;background:var(--teal)}
.brand .name{font-family:"Montserrat",sans-serif;font-weight:700;font-size:27px;color:var(--teal);letter-spacing:.5px;line-height:1.1}
.nav{font-size:13.5px;color:#333}
.nav a{color:inherit;text-decoration:none;position:absolute;white-space:nowrap}
.nav a.active{color:var(--teal)}

.hero{left:0;top:144px;width:1200px;height:524px;background:linear-gradient(90deg,#b7a487 0%,#c9c0b0 30%,#a9a59a 55%,#8d8f86 75%,#a8aa9f 100%)}
.hero .lawn{left:0;top:390px;width:1200px;height:134px;background:linear-gradient(180deg,rgba(96,140,52,.0),rgba(96,140,52,.85))}
.hero-arrow{top:216px;width:47px;height:58px;background:rgba(255,255,255,.85);display:flex;align-items:center;justify-content:center}
.hero-caption{left:98px;top:421px;height:47px;padding:0 16px;background:rgba(23,168,140,.9);color:#fff;font-family:"Montserrat",sans-serif;font-weight:500;font-size:21px;line-height:47px;white-space:nowrap}

.quote-band{left:0;top:668px;width:1200px;height:82px;background:var(--dark)}
.quote-band .line{left:119px;top:28px;color:#fff;font-family:"Montserrat",sans-serif;font-weight:500;font-size:20px;white-space:nowrap}
.btn-quote{left:855px;top:20px;width:225px;height:44px;background:var(--green);color:#fff;font-family:"Montserrat",sans-serif;font-size:16px;letter-spacing:.5px;text-align:center;line-height:44px;white-space:nowrap}

.feature{top:830px;width:270px;text-align:center}
.feature svg{display:block;margin:0 auto 20px}
.feature h3{font-family:Arial,sans-serif;font-weight:700;font-size:18px;color:#333;margin-bottom:20px}
.feature p{font-size:12.5px;line-height:19px;color:var(--muted)}
.divider-v{top:863px;width:1px;height:109px;background:var(--line)}

.about{left:0;top:1091px;width:1200px;height:354px;background:var(--soft)}
.about .photo{left:98px;top:69px;width:322px;height:241px;background:linear-gradient(180deg,#5d7fb8 0%,#8ea2c3 45%,#b19374 70%,#3e6a2c 100%)}
.about h2{left:471px;top:62px;font-family:Arial,sans-serif;font-weight:700;font-size:26px;color:#333}
.about p{left:475px;top:108px;width:620px;font-family:Arial,sans-serif;font-size:12px;line-height:18.6px;color:#555}
.btn-teal{background:var(--teal);color:#fff;font-size:14px;text-align:center}
.about .btn-teal{left:478px;top:282px;width:117px;height:33px;line-height:33px}

.section-title{left:0;top:1503px;width:1200px;text-align:center;font-family:Arial,sans-serif;font-weight:700;font-size:26px;color:#333}
.card{top:1564px;width:319px;height:387px;border:1px solid #e3e3e3;background:#fff}
.card .img{left:15px;top:15px;width:287px;height:170px}
.card .tag{left:0;bottom:12px;padding:0 12px;height:30px;line-height:30px;background:rgba(20,20,20,.8);color:#fff;font-size:12.5px;white-space:nowrap}
.card h4{left:15px;top:199px;font-size:15px;font-weight:600;color:#333}
.card .specs{left:15px;top:226px;width:287px;height:34px;border-top:1px solid #ccc;border-bottom:1px solid #ccc;display:flex;font-size:12px;color:#555}
.card .specs span{flex:1;display:flex;align-items:center;gap:6px;padding-left:2px;border-right:1px solid #ccc;white-space:nowrap}
.card .specs span:last-child{border-right:0;justify-content:flex-end}
.card .desc{left:15px;top:274px;width:287px;font-size:11px;line-height:16.5px;color:#777}
.card .price{left:15px;top:347px;font-size:17px;color:var(--price)}
.card .btn{left:211px;top:343px;width:92px;height:27px;line-height:27px;text-align:center;color:#fff;font-size:13px}

.footer{left:0;top:2040px;width:1200px;height:244px;background:var(--footer);color:#fff}
.footer h5{font-size:12.5px;font-weight:600;letter-spacing:.3px;margin-bottom:16px}
.footer p{font-size:11.5px;line-height:17px}
.footer .col{top:38px}
.footer ul{list-style:none;font-size:11.5px;line-height:20px}
.footer ul li::before{content:"";display:inline-block;width:6px;height:6px;border-radius:50%;background:#fff;margin-right:14px;vertical-align:middle}
.footer .info{display:flex;align-items:center;gap:10px;font-size:11.5px;line-height:20px}
.field{width:196px;height:28px;background:#3a3a3a;color:#fff;font-size:11px;padding-left:10px;line-height:28px;margin-bottom:8px;position:relative}
.btn-contact{background:var(--green);color:#fff;font-size:12px;text-align:center;width:76px;height:25px;line-height:25px;margin-left:120px;margin-top:12px}

.base{left:0;top:2284px;width:1200px;height:57px;background:var(--footer-base);color:#fff;font-size:11px}
.social{left:1010px;top:20px;display:flex;gap:16px}
.social span{width:16px;height:16px;border-radius:50%;background:#fff}
</style>
</head>
<body>

<div class="abs topbar">
  <div class="abs welcome">Welcome To Our Site</div>
  <div class="abs phone">
    <svg width="8" height="12" viewBox="0 0 8 12"><rect x="0.5" y="0.5" width="7" height="11" rx="1.5" fill="none" stroke="#fff"/><rect x="3" y="9" width="2" height="1" fill="#fff"/></svg>
    +00-555-0142
  </div>
  <div class="abs sep"></div>
  <div class="abs mail">
    <svg width="13" height="10" viewBox="0 0 13 10"><rect width="13" height="10" fill="#fff"/><path d="M0 0l6.5 5L13 0" fill="none" stroke="#17a88c"/></svg>
    info@lanterndwelling.example
  </div>
</div>

<div class="abs header">
  <div class="abs brand" style="left:98px;top:18px">
    <div class="mark"></div>
    <div class="name">Lantern Dwelling<br>Partners</div>
  </div>
  <nav class="abs nav" style="left:0;top:40px">
    <a class="active" style="left:596px">Home</a>
    <a style="left:671px">About Us</a>
    <a style="left:764px">Services</a>
    <a style="left:851px">Properties</a>
    <a style="left:952px">Gallery</a>
    <a style="left:1032px">Contact Us</a>
  </nav>
</div>

<section class="abs hero" role="img" aria-label="Smiling couple in front of their new suburban home with a green lawn">
  <div class="abs lawn"></div>
  <div class="abs hero-arrow" style="left:0"><svg width="10" height="14" viewBox="0 0 10 14"><path d="M8 1L2 7l6 6" fill="none" stroke="#333" stroke-width="2"/></svg></div>
  <div class="abs hero-arrow" style="left:1153px"><svg width="10" height="14" viewBox="0 0 10 14"><path d="M2 1l6 6-6 6" fill="none" stroke="#333" stroke-width="2"/></svg></div>
  <div class="abs hero-caption">Specializing in “warm environments</div>
</section>

<div class="abs quote-band">
  <div class="abs line">Etiam sit amet lacinia leo. In consequat euismod odio nec rhoncus</div>
  <div class="abs btn-quote">REQUEST A QUOTE</div>
</div>

<div class="abs feature" style="left:99px">
  <svg width="70" height="50" viewBox="0 0 70 50"><rect x="12" y="4" width="26" height="44" fill="#666"/><g fill="#fff"><rect x="16" y="9" width="4" height="4"/><rect x="23" y="9" width="4" height="4"/><rect x="30" y="9" width="4" height="4"/><rect x="16" y="17" width="4" height="4"/><rect x="23" y="17" width="4" height="4"/><rect x="30" y="17" width="4" height="4"/><rect x="16" y="25" width="4" height="4"/><rect x="23" y="25" width="4" height="4"/><rect x="30" y="25" width="4" height="4"/><rect x="16" y="33" width="4" height="4"/><rect x="30" y="33" width="4" height="4"/></g><path d="M42 30l10-10 12 12-10 10z" fill="none" stroke="#666" stroke-width="2.5"/><circle cx="52" cy="25" r="2" fill="#666"/></svg>
  <h3>REAL ESTATE</h3>
  <p>Phasellus nec turpis vitae sem volutpat fauci-bus sit amet non nunc. Phasellus semper urna egestas quam porta, sed gravida augue tincidunt. Maecenas</p>
</div>
<div class="abs divider-v" style="left:421px"></div>
<div class="abs feature" style="left:469px">
  <svg width="70" height="50" viewBox="0 0 70 50"><path d="M4 18l12-8 10 4 8-4 10 0 12 8 10-6v14l-8 6-14 12-6-4-6 4-8-6-10-6-10 2z" fill="#666"/><path d="M26 22l8-4 8 6" fill="none" stroke="#fff" stroke-width="2"/></svg>
  <h3>BROKERAGE</h3>
  <p>Phasellus nec turpis vitae sem volutpat fauci-bus sit amet non nunc. Phasellus semper urna egestas quam porta, sed gravida augue tincidunt. Maecenas</p>
</div>
<div class="abs divider-v" style="left:791px"></div>
<div class="abs feature" style="left:837px">
  <svg width="70" height="50" viewBox="0 0 70 50"><path d="M35 6L12 26h6v20h34V26h6z" fill="#666"/><rect x="30" y="32" width="10" height="14" fill="#fff"/></svg>
  <h3>BOUTIQUE HOUSING</h3>
  <p>Phasellus nec turpis vitae sem volutpat fauci-bus sit amet non nunc. Phasellus semper urna egestas quam porta, sed gravida augue tincidunt. Maecenas</p>
</div>

<section class="abs about">
  <div class="abs photo" role="img" aria-label="Two-storey family house at dusk with lit windows and garage"></div>
  <h2 class="abs">ABOUT US</h2>
  <p class="abs">Vestibulum tristique vestibulum suscipit. Cras dapibus metus ut odio pulvinar, non tincidunt eros aliquam. Vivamus bibendum enim a elementum faucibus. Fusce auctor lorem non sem suscipit, rutrum mattis nisi auctor. Nulla tempus nulla at nisi dictum, vitae dignissim mi hendrerit. Donec convallis erat risus, eget venenatis est sagittis et. Fusce mi augue, porta nec sapien a, tempus tincidunt urna. Lorem ipsum dolor sit amet, consectetur adipiscing elit. Nullam sit amet lorem nisi. Nunc purus velit, feugiat et odio in, efficitur viverra ante. Quisque tellus libero, tempus ac turpis vel, dapibus venenatis lorem. Phasellus consectetur libero in justo sodales, at pretium velit luctus. Vestibulum ante ipsum primis in faucibus orci luctus et ultrices posuere cubilia Curae; Phasellus elementum dictum nisi sed tempus. Donec id tellus metus.</p>
  <div class="abs btn-teal">Read More</div>
</section>

<h2 class="abs section-title">OUR PROPERTIES</h2>

<article class="abs card" style="left:100px">
  <div class="abs img" role="img" aria-label="Large grey family house with garage at dusk" style="background:linear-gradient(180deg,#6d8dc4,#9aa7bd 55%,#8c7a66)"><div class="abs tag">Lorem ipsum dolor sit</div></div>
  <h4 class="abs">Contantry Popilar</h4>
  <div class="abs specs">
    <span><svg width="16" height="10" viewBox="0 0 16 10"><path d="M1 0v10M1 7h14v3M1 5h14V3H6" fill="none" stroke="#666" stroke-width="1.5"/></svg>Beds:3</span>
    <span style="padding-left:12px"><svg width="14" height="12" viewBox="0 0 14 12"><path d="M1 6h12v3H1zM3 1h3v5" fill="none" stroke="#666" stroke-width="1.5"/></svg>Bath:3</span>
    <span><svg width="16" height="10" viewBox="0 0 16 10"><path d="M2 5l2-4h8l2 4v4H2z" fill="#666"/></svg>Car Park</span>
  </div>
  <p class="abs desc">Lorem ipsum dolor sit amet, con id sa idsectetur adipi-scing elit. Ut et tincidunt massa, eget luctus eros. Vivamus ut odio imperdiet ipsum volutpat mattis luctus vitae lectus.</p>
  <div class="abs price">$329.34</div>
  <div class="abs btn" style="background:var(--green)">Details</div>
</article>

<article class="abs card" style="left:442px">
  <div class="abs img" role="img" aria-label="Wooden deck patio of a modern house with outdoor seating at evening" style="background:linear-gradient(180deg,#3b3a38,#8b7863 55%,#a06b44)"><div class="abs tag">Popilar sit amit</div></div>
  <h4 class="abs">Loreme ipsum dolor</h4>
  <div class="abs specs">
    <span><svg width="16" height="10" viewBox="0 0 16 10"><path d="M1 0v10M1 7h14v3M1 5h14V3H6" fill="none" stroke="#666" stroke-width="1.5"/></svg>Beds:3</span>
    <span style="padding-left:12px"><svg width="14" height="12" viewBox="0 0 14 12"><path d="M1 6h12v3H1zM3 1h3v5" fill="none" stroke="#666" stroke-width="1.5"/></svg>Bath:3</span>
    <span><svg width="16" height="10" viewBox="0 0 16 10"><path d="M2 5l2-4h8l2 4v4H2z" fill="#666"/></svg>Car Park</span>
  </div>
  <p class="abs desc">Lorem ipsum dolor sit amet, con id sa idsectetur adipi-scing elit. Ut et tincidunt massa, eget luctus eros. Vivamus ut odio imperdiet ipsum volutpat mattis luctus vitae lectus.</p>
  <div class="abs price">$329.34</div>
  <div class="abs btn" style="background:var(--teal)">Details</div>
</article>

<article class="abs card" style="left:782px">
  <div class="abs img" role="img" aria-label="White cottage-style house among green trees" style="background:linear-gradient(180deg,#7fb0d8,#d8dcdc 45%,#6f9a4a)"><div class="abs tag">Lorem ipsum dolor sit</div></div>
  <h4 class="abs">Loreme ipsum dolor</h4>
  <div class="abs specs">
    <span><svg width="16" height="10" viewBox="0 0 16 10"><path d="M1 0v10M1 7h14v3M1 5h14V3H6" fill="none" stroke="#666" stroke-width="1.5"/></svg>Beds:3</span>
    <span style="padding-left:12px"><svg width="14" height="12" viewBox="0 0 14 12"><path d="M1 6h12v3H1zM3 1h3v5" fill="none" stroke="#666" stroke-width="1.5"/></svg>Bath:3</span>
    <span><svg width="16" height="10" viewBox="0 0 16 10"><path d="M2 5l2-4h8l2 4v4H2z" fill="#666"/></svg>Car Park</span>
  </div>
  <p class="abs desc">Lorem ipsum dolor sit amet, con id sa idsectetur adipi-scing elit. Ut et tincidunt massa, eget luctus eros. Vivamus ut odio imperdiet ipsum volutpat mattis luctus vitae lectus.</p>
  <div class="abs price">$329.34</div>
  <div class="abs btn" style="background:var(--teal)">Details</div>
</article>

<footer class="abs footer">
  <div class="abs col" style="left:111px;width:225px">
    <h5>WHO WE ARE</h5>
    <p>Lorem ipsum dolor sit amet, consectetur adipiscing elit. Nullam venenatis velit blandit est condimentum aliquet. Curabitur ut libero justo. Nulla ut ex facilisis, tincidunt quam vitae, iaculis orci. Nullam eu faucibus nibh.</p>
    <div style="margin-top:20px;margin-left:160px;display:flex;align-items:center;gap:8px;font-size:12px">More
      <svg width="13" height="13" viewBox="0 0 13 13"><circle cx="6.5" cy="6.5" r="5.8" fill="none" stroke="#fff"/><path d="M4 6.5h5M7 4.5l2 2-2 2" fill="none" stroke="#fff"/></svg></div>
  </div>
  <div class="abs col" style="left:420px">
    <h5>USEFUL LINKS</h5>
    <ul><li>Home</li><li>About Us</li><li>Service</li><li>FAQ</li><li>Sitemap</li><li>Contact Us</li></ul>
  </div>
  <div class="abs col" style="left:621px;width:230px">
    <h5>GET IN TOUCH</h5>
    <p style="margin-bottom:10px">Doloreiur quia commolu ptatemp dolupta oreprerum tibusam eumenis et consent acculignis dentibea</p>
    <div class="info"><svg width="9" height="12" viewBox="0 0 9 12"><path d="M4.5 12S0 6.5 0 4.5a4.5 4.5 0 019 0C9 6.5 4.5 12 4.5 12z" fill="#fff"/><circle cx="4.5" cy="4.5" r="1.6" fill="#222"/></svg>84 Street, City, State 24813</div>
    <div class="info"><svg width="11" height="11" viewBox="0 0 11 11"><path d="M2 0l2 3-1.2 1.3a7 7 0 003.9 3.9L8 7l3 2-1 2C5 11 0 6 0 1z" fill="#fff"/></svg>(555) 38 - 394 - 0182</div>
    <div class="info"><svg width="11" height="8" viewBox="0 0 11 8"><rect width="11" height="8" fill="#fff"/><path d="M0 0l5.5 4L11 0" fill="none" stroke="#222"/></svg>yoursite@yourmail.com</div>
  </div>
  <div class="abs col" style="left:910px">
    <h5>CONTACT</h5>
    <p style="width:200px;margin-bottom:14px">Doloreiur quia commolu ptatemp dolupta oreprerum</p>
    <div class="field">Email</div>
    <div class="field">Contact For
      <svg style="position:absolute;right:10px;top:11px" width="9" height="6" viewBox="0 0 9 6"><path d="M1 1l3.5 3.5L8 1" fill="none" stroke="#fff" stroke-width="1.4"/></svg></div>
    <div class="btn-contact">CONTACT</div>
  </div>
</footer>

<div class="abs base">
  <div class="abs" style="left:109px;top:21px">© 2016 yoursite. All rights reserved.</div>
  <div class="abs social"><span></span><span></span><span></span><span></span></div>
</div>

</body>
</html>
```